RTavenor Business Cards & Letterhead

I have a logo but need a design for some new business cards. We are a Design-Build Firm that specializes in the design and construction of commercial projects.
the cards need to be professional. no cartoon stuff.
i would like to have the cards in AI format so I can update the card as needed. Logo is provided.
Our Address is: 4187 Marlowe Ct. Linden Ridge, Westmoor 27614

```html
<!DOCTYPE html>
<html lang="en">
<head>
<meta charset="utf-8">
<title>RTavenor Business Cards</title>
<link href="https://fonts.googleapis.com/css2?family=Open+Sans:wght@400;700;800&display=swap" rel="stylesheet">
<style>
  :root {
    --stage: #e4e7ec;
    --paper: #ffffff;
    --ink: #2b2b2b;
    --ink-soft: #3a3a3a;
    --brand-blue: #1a66b0;
    --brand-deep: #0d4a82;
    --back-light: #1e78c2;
    --back-dark: #0b3f6e;
    --back-mark: #0f4677;
  }
  * { box-sizing: border-box; margin: 0; padding: 0; }
  html, body { width: 1200px; height: 780px; overflow: hidden; }
  body {
    background: var(--stage);
    font-family: "Open Sans", Arial, sans-serif;
    display: flex;
    align-items: center;
    justify-content: center;
    gap: 40px;
  }
  .card {
    position: relative;
    width: 500px;
    height: 286px;
    overflow: hidden;
    box-shadow: 0 6px 18px rgba(0,0,0,0.18);
  }
  .card-front { background: var(--paper); color: var(--ink); }
  .brand {
    position: absolute;
    left: 26px;
    top: 24px;
    display: flex;
    align-items: center;
    gap: 8px;
  }
  .brand-square { width: 22px; height: 22px; background: var(--brand-blue); }
  .brand-name {
    font-weight: 800;
    font-size: 32px;
    letter-spacing: 0.5px;
    color: var(--ink-soft);
    line-height: 1;
  }
  .contact {
    position: absolute;
    left: 30px;
    top: 92px;
    font-size: 12.5px;
    line-height: 17px;
    color: var(--ink);
  }
  .contact .address { margin-bottom: 2px; }
  .contact-row { display: flex; align-items: center; gap: 6px; }
  .contact-row svg { width: 11px; height: 11px; flex: none; }
  .person {
    position: absolute;
    right: 40px;
    top: 96px;
    text-align: right;
  }
  .person-name {
    font-weight: 700;
    font-size: 21px;
    letter-spacing: 0.6px;
    color: var(--brand-blue);
    text-transform: uppercase;
    line-height: 1.1;
  }
  .person-title { font-size: 13px; color: var(--ink); margin-top: 2px; }
  .name-tab {
    position: absolute;
    right: 0;
    top: 96px;
    width: 24px;
    height: 44px;
    background: linear-gradient(90deg, var(--brand-blue), var(--brand-deep));
  }
  .card-back {
    background: radial-gradient(ellipse at 45% 40%, var(--back-light) 0%, var(--brand-deep) 55%, var(--back-dark) 100%);
    display: flex;
    align-items: center;
    justify-content: center;
  }
  .back-brand {
    font-weight: 800;
    font-size: 56px;
    letter-spacing: 1px;
    color: var(--back-mark);
  }
</style>
</head>
<body>
  <section class="card card-front" aria-label="Business card front">
    <div class="brand">
      <span class="brand-square"></span>
      <span class="brand-name">RTAVENOR</span>
    </div>
    <div class="contact">
      <p class="address">4187 Marlowe Ct. Linden Ridge,<br>Westmoor 27614</p>
      <p class="contact-row">
        <svg viewBox="0 0 12 12"><circle cx="6" cy="6" r="6" fill="var(--brand-blue)"/><path d="M4 3.2c.4-.3.7-.2.9.2l.4.8c.1.3 0 .5-.2.7l-.3.2c.3.7.8 1.2 1.5 1.5l.2-.3c.2-.2.4-.3.7-.2l.8.4c.4.2.5.5.2.9-.6.8-1.5.8-2.6.1-.9-.6-1.6-1.3-2.1-2.2-.5-.9-.5-1.6.5-2.1z" fill="#fff"/></svg>
        (555) 555-0148
      </p>
      <p class="contact-row">
        <svg viewBox="0 0 12 12"><circle cx="6" cy="6" r="6" fill="var(--brand-blue)"/><circle cx="6" cy="6" r="3.4" fill="none" stroke="#fff" stroke-width="0.8"/><path d="M2.6 6h6.8M6 2.6c-1.4 1.8-1.4 5 0 6.8M6 2.6c1.4 1.8 1.4 5 0 6.8" fill="none" stroke="#fff" stroke-width="0.7"/></svg>
        www.rtavenor.com
      </p>
      <p class="contact-row">
        <svg viewBox="0 0 12 12"><circle cx="6" cy="6" r="6" fill="var(--brand-blue)"/><rect x="3" y="3.8" width="6" height="4.4" fill="none" stroke="#fff" stroke-width="0.8"/><path d="M3 3.9l3 2.4 3-2.4" fill="none" stroke="#fff" stroke-width="0.8"/></svg>
        GRT@RTavenor.com
      </p>
    </div>
    <div class="person">
      <p class="person-name">Gavin Tavenor</p>
      <p class="person-title">Founder/President</p>
    </div>
    <span class="name-tab"></span>
  </section>

  <section class="card card-back" aria-label="Business card back">
    <span class="back-brand">RTAVENOR</span>
  </section>
</body>
</html>
```